Creative, Colorful, Dynamic Infographic for Global Non-Profit

We are a global arts and education non-profit in need of an infographic that illustrates four key skills embedded in our work: Curiosity, Listening, Imagination, Postive Action.
We work primarily with educators, students, and artists who use the power of personal stories to build community and connection and to bridge divides.
Our new brand guidelines, logos, and fonts are here: https://stylevault.example/lumen-circle
I've attached a mock-up of the graphic and the required text. (Note the attached design was created by a staff person, your final design does not need to be the same. The color scheme and text of the final design should match the brand guidelines above.)
The graphic will be used for both web and print media and should include the purple Lumen Circle logo (also attached).
Ideally the final design will delight audiences and spark interest in our work.

```html
<!DOCTYPE html>
<html lang="en">
<head>
<meta charset="utf-8">
<title>Lumen Circle – Four Skills Infographic</title>
<link rel="stylesheet" href="https://fonts.googleapis.com/css2?family=Hanken+Grotesk:wght@400;700&display=swap">
<style>
  :root {
    --purple: #663399;
    --red: #ee4444;
    --yellow: #e8cb48;
    --blue: #236bbf;
    --navy: #1e1e3a;
    --white: #ffffff;
    --paper: #ffffff;
  }
  html, body {
    margin: 0;
    padding: 0;
    width: 1148px;
    height: 1200px;
    overflow: hidden;
    background: var(--paper);
  }
  .infographic {
    display: block;
    width: 1148px;
    height: 1200px;
    font-family: "Hanken Grotesk", Arial, sans-serif;
  }
  .title { fill: var(--purple); font-size: 74px; font-weight: 400; }
  .brand-name { fill: var(--white); font-weight: 700; }
  .petal--purple, .fill--purple { fill: var(--purple); }
  .petal--red, .fill--red { fill: var(--red); }
  .petal--yellow, .fill--yellow { fill: var(--yellow); }
  .petal--blue, .fill--blue { fill: var(--blue); }
  .skill-halo { fill: var(--white); }
  .skill-ring { fill: var(--white); stroke-width: 33; }
  .skill-ring--purple { stroke: var(--purple); }
  .skill-ring--red { stroke: var(--red); }
  .skill-ring--yellow { stroke: var(--yellow); }
  .skill-ring--blue { stroke: var(--blue); }
  .skill-text { fill: var(--navy); font-size: 37px; text-anchor: middle; }
  .skill-name { font-weight: 700; }
  .petal-text { fill: var(--white); font-size: 33px; text-anchor: middle; }
  .petal-text--dark { fill: var(--navy); }
  .arrow-badge { stroke: var(--white); stroke-width: 4; }
  .arrow { fill: var(--white); }
  .hub { fill: var(--purple); stroke: var(--white); stroke-width: 8; }
  .icon-slot--dark { fill: var(--navy); }
  .icon-slot--light { fill: var(--white); }
  .tick-disc--dark { fill: var(--navy); }
  .tick-disc--light { fill: var(--white); }
  .tick { fill: none; stroke-width: 5; stroke-linecap: round; stroke-linejoin: round; }
  .tick--light { stroke: var(--white); }
  .tick--red { stroke: var(--red); }
</style>
</head>
<body>
<svg class="infographic" viewBox="0 0 1850 1935" width="1148" height="1200" xmlns="http://www.w3.org/2000/svg">

  <!-- Header -->
  <g class="header">
    <circle class="fill--purple" cx="488" cy="180" r="62"/>
    <text class="brand-name" x="488" y="176" font-size="22" text-anchor="middle">Lumen</text>
    <text class="brand-name" x="488" y="202" font-size="22" text-anchor="middle">Circle</text>
    <text class="title" x="580" y="207">INFOGRAPHICS WITH ICONS</text>
  </g>

  <!-- Petals -->
  <path class="petal--red" d="M888,245 L957,245 A189,190 0 0 0 1146,435 L1146,1045 L922,1045 L922,810 L698,810 L698,435 A190,189 0 0 0 888,245 Z"/>
  <path class="petal--purple" d="M320,810 L922,810 L922,1045 L698,1045 L698,1255 L320,1255 A188,190 0 0 0 133,1065 L133,997 A188,187 0 0 0 320,810 Z"/>
  <path class="petal--blue" d="M1146,810 L1527,810 A188,187 0 0 0 1715,997 L1715,1065 A188,190 0 0 0 1527,1255 L922,1255 L922,1045 L1146,1045 Z"/>
  <path class="petal--yellow" d="M698,1045 L922,1045 L922,1255 L1146,1255 L1146,1630 A189,190 0 0 0 957,1820 L888,1820 A190,190 0 0 0 698,1630 Z"/>

  <!-- Petal content -->
  <g class="petal-content petal-content--red">
    <circle class="tick-disc--light" cx="928" cy="320" r="22"/>
    <path class="tick tick--red" d="M917,320 L925,329 L940,311"/>
    <rect class="icon-slot--light" role="img" aria-label="Open hand offering icon" x="866" y="350" width="96" height="30" rx="10"/>
    <text class="petal-text">
      <tspan x="924" y="448">Your positive actions</tspan>
      <tspan x="924" y="493">lead to curiosity</tspan>
      <tspan x="924" y="538">about what else</tspan>
      <tspan x="924" y="583">is possible</tspan>
    </text>
  </g>
  <g class="petal-content petal-content--purple">
    <rect class="icon-slot--light" role="img" aria-label="Person with an idea icon" x="216" y="984" width="64" height="84" rx="14"/>
    <text class="petal-text">
      <tspan x="389" y="998">Your curiosity</tspan>
      <tspan x="389" y="1043">allows you</tspan>
      <tspan x="389" y="1088">to listen</tspan>
    </text>
  </g>
  <g class="petal-content petal-content--blue">
    <rect class="icon-slot--light" role="img" aria-label="Head with brain icon" x="1468" y="876" width="48" height="72" rx="18"/>
    <text class="petal-text">
      <tspan x="1480" y="998">Your imagination</tspan>
      <tspan x="1480" y="1043">can spark</tspan>
      <tspan x="1480" y="1088">positive action</tspan>
    </text>
  </g>
  <g class="petal-content petal-content--yellow">
    <rect class="icon-slot--dark" role="img" aria-label="Person listening icon" x="890" y="1440" width="64" height="56" rx="14"/>
    <text class="petal-text petal-text--dark">
      <tspan x="922" y="1535">Your listening</tspan>
      <tspan x="922" y="1580">allows you to</tspan>
      <tspan x="922" y="1625">take in new</tspan>
      <tspan x="922" y="1670">information</tspan>
    </text>
  </g>

  <!-- Skill circles -->
  <g class="skill skill--curiosity">
    <circle class="skill-halo" cx="637" cy="750" r="256"/>
    <circle class="skill-ring skill-ring--purple" cx="637" cy="750" r="232"/>
    <rect class="icon-slot--dark" role="img" aria-label="Person with an idea icon" x="598" y="556" width="80" height="106" rx="16"/>
    <text class="skill-text">
      <tspan class="skill-name" x="637" y="703">Curiosity –</tspan>
      <tspan x="637" y="748">Focus on how you can</tspan>
      <tspan x="637" y="793">learn from another's</tspan>
      <tspan x="637" y="838">knowledge and</tspan>
      <tspan x="637" y="883">experience</tspan>
    </text>
  </g>

  <g class="skill skill--positive-action">
    <circle class="skill-halo" cx="1207" cy="750" r="256"/>
    <circle class="skill-ring skill-ring--red" cx="1207" cy="750" r="232"/>
    <circle class="tick-disc--dark" cx="1225" cy="621" r="22"/>
    <path class="tick tick--light" d="M1214,621 L1222,630 L1237,612"/>
    <rect class="icon-slot--dark" role="img" aria-label="Open hand offering icon" x="1163" y="650" width="96" height="30" rx="10"/>
    <text class="skill-text">
      <tspan class="skill-name" x="1211" y="723">Positive action -</tspan>
      <tspan x="1211" y="768">Show your words</tspan>
      <tspan x="1211" y="813">and actions</tspan>
      <tspan x="1211" y="858">matter</tspan>
    </text>
  </g>

  <g class="skill skill--listening">
    <circle class="skill-halo" cx="637" cy="1315" r="256"/>
    <circle class="skill-ring skill-ring--yellow" cx="637" cy="1315" r="232"/>
    <rect class="icon-slot--dark" role="img" aria-label="Person listening icon" x="584" y="1188" width="84" height="74" rx="16"/>
    <text class="skill-text">
      <tspan class="skill-name" x="635" y="1308">Listening –</tspan>
      <tspan x="635" y="1353">Seek to</tspan>
      <tspan x="635" y="1398">understand</tspan>
      <tspan x="635" y="1443">before speaking</tspan>
    </text>
  </g>

  <g class="skill skill--imagination">
    <circle class="skill-halo" cx="1207" cy="1315" r="256"/>
    <circle class="skill-ring skill-ring--blue" cx="1207" cy="1315" r="232"/>
    <rect class="icon-slot--dark" role="img" aria-label="Head with brain icon" x="1183" y="1176" width="48" height="74" rx="18"/>
    <text class="skill-text">
      <tspan class="skill-name" x="1206" y="1284">Imagination –</tspan>
      <tspan x="1206" y="1329">Consider</tspan>
      <tspan x="1206" y="1374">possibilities beyond</tspan>
      <tspan x="1206" y="1419">what you know</tspan>
    </text>
  </g>

  <!-- Flow arrows -->
  <g class="flow-arrow flow-arrow--left">
    <rect class="arrow-badge fill--red" x="913" y="697" width="134" height="102" rx="18"/>
    <path class="arrow" d="M945,748 L978,715 L992,729 L980,741 L1016,741 L1016,755 L980,755 L992,767 L978,781 Z"/>
  </g>
  <g class="flow-arrow flow-arrow--down">
    <rect class="arrow-badge fill--purple" x="589" y="908" width="102" height="134" rx="18"/>
    <path class="arrow" d="M640,1008 L607,975 L621,961 L633,973 L633,938 L647,938 L647,973 L659,961 L673,975 Z"/>
  </g>
  <g class="flow-arrow flow-arrow--right">
    <rect class="arrow-badge fill--yellow" x="796" y="1263" width="134" height="102" rx="18"/>
    <path class="arrow" d="M898,1314 L865,1347 L851,1333 L863,1321 L828,1321 L828,1307 L863,1307 L851,1295 L865,1281 Z"/>
  </g>
  <g class="flow-arrow flow-arrow--up">
    <rect class="arrow-badge fill--blue" x="1157" y="1023" width="102" height="134" rx="18"/>
    <path class="arrow" d="M1208,1056 L1241,1089 L1227,1103 L1215,1091 L1215,1126 L1201,1126 L1201,1091 L1189,1103 L1175,1089 Z"/>
  </g>

  <!-- Hub -->
  <g class="hub-brand">
    <circle class="hub" cx="922" cy="1037" r="126"/>
    <text class="brand-name" x="922" y="1027" font-size="44" text-anchor="middle">Lumen</text>
    <text class="brand-name" x="922" y="1077" font-size="44" text-anchor="middle">Circle</text>
  </g>
</svg>
</body>
</html>
```